High Tech Real Estate Startup needs a business card

We are developing an innovative real estate marketing product based around advanced search and virtual reality.

We talk to people, we need business cards.

Target Market(s)

The target market is technology professionals and realtors.

Contact Information for Business Card

The information to be included will include

Name
Title
Phone Number
E-mail Address
www.zelquin.com

It should use simple iconography for each one of those fields.

Font styles to use
Other font styles liked:
• Co, Jubilat, Avenir

Colors

Designer to choose colors to be used in the design.

Requirements
Must have
• Clean aesthetic,
• Good use of negative space.
• It should use our company logo, shown in the attached file. It is able to use the negative of that logo (coloured font and white background) and I have attached other acceptable accent colours in a swatch file.
Should not have
• Should not be too busy
• No extraneous text (slogans, tag lines etc)

```html
<!DOCTYPE html>
<html lang="en">
<head>
<meta charset="UTF-8">
<title>Zelquin Business Card</title>
<link href="https://fonts.googleapis.com/css2?family=Open+Sans:wght@400;600&display=swap" rel="stylesheet">
<style>
  :root {
    --backdrop: #3b3b3d;
    --card: #232325;
    --teal: #3fbcc0;
    --ink-light: #f1f1f1;
    --ink-soft: #d8d8d8;
  }
  * { margin: 0; padding: 0; box-sizing: border-box; }
  html, body {
    width: 799px;
    height: 1200px;
    overflow: hidden;
    background: var(--backdrop);
    font-family: "Open Sans", Arial, sans-serif;
  }
  .canvas {
    width: 799px;
    height: 1200px;
    display: flex;
    flex-direction: column;
    align-items: center;
    justify-content: space-around;
    padding: 60px 0;
  }
  .card {
    width: 580px;
    height: 332px;
    background: var(--card);
    border-radius: 26px;
    box-shadow: 0 10px 28px rgba(0, 0, 0, 0.35);
    display: flex;
    align-items: center;
    justify-content: center;
  }
  .brand-name {
    color: var(--teal);
    font-weight: 600;
    font-size: 68px;
    letter-spacing: 4px;
  }
  .contact-block {
    display: flex;
    flex-direction: column;
    align-items: center;
    text-align: center;
  }
  .person-name {
    color: var(--teal);
    font-weight: 600;
    font-size: 24px;
    letter-spacing: 0.5px;
  }
  .person-title {
    color: var(--ink-soft);
    font-size: 12.5px;
    margin-top: 4px;
  }
  .divider {
    width: 230px;
    height: 1px;
    margin: 10px 0 14px;
    background: linear-gradient(90deg, transparent, var(--teal), transparent);
  }
  .contact-line {
    color: var(--ink-light);
    font-size: 14px;
    line-height: 1.35;
  }
</style>
</head>
<body>
  <main class="canvas">
    <section class="card card-front">
      <span class="brand-name">ZELQUIN</span>
    </section>
    <section class="card card-back">
      <div class="contact-block">
        <h1 class="person-name">John Doe Smith</h1>
        <p class="person-title">Managing Director</p>
        <div class="divider"></div>
        <p class="contact-line">555.555.5555</p>
        <p class="contact-line">johndoe@zelquin.com</p>
        <p class="contact-line">www.zelquin.com</p>
      </div>
    </section>
  </main>
</body>
</html>
```